Fenwick Grading LTD - website for irrigation & Landscape Lighting & Buried service wire

Looking for a website to help promote my business with Irrigation (installation, service, etc) and buried service wire/drainage solutions.

Commercial/Residential

Landscape lighting.

I’ll get photos in the trucks and trailers to upload as well maybe the machine as well.

Target Market(s)

Homeowners who want green grass and beautiful gardens. Beautiful landscape lighting

Industry/Entity Type

Irrigation systems and landscape lighting and buried service wire to homes and offering Drainage soltions.

Coding

Coded - Design and coding required

Number of Pages Required

4 page

Colors
F0912C
F2A743
F7CA91
FBE8D2
FDF5EE

Requirements
Must have
• was hoping to link up my email on fenwickgrading@mailbox-example.net with the website if possible.
Nice to have
• Page for Irrigation, page for landscape lighting, page buried service wire & drainage soltions.

```html
<!DOCTYPE html>
<html lang="en">
<head>
<meta charset="utf-8">
<title>Fenwick Grading LTD</title>
<link rel="stylesheet" href="https://fonts.googleapis.com/css2?family=Josefin+Sans:wght@400;600;700&display=swap">
<style>
:root{
  --orange:#F0912C;
  --orange-2:#F2A743;
  --peach:#F7CA91;
  --cream:#FBE8D2;
  --ivory:#FDF5EE;
  --ink:#1d1d1d;
  --text:#3a3a3a;
  --black:#000;
  --white:#fff;
}
*{margin:0;padding:0;box-sizing:border-box}
html,body{width:1200px;height:3971px;overflow:hidden}
body{position:relative;font-family:"Josefin Sans",sans-serif;color:var(--ink);background:var(--white)}
.abs{position:absolute}
.btn{position:absolute;display:flex;align-items:center;justify-content:center;background:var(--orange);color:var(--white);font-weight:600;font-size:12px}

/* header */
.header{left:0;top:0;width:1200px;height:70px;background:var(--white);z-index:3}
.brand{display:flex;align-items:center;gap:8px;color:var(--orange);font-weight:700;font-size:17px}
.brand-dot{width:14px;height:14px;border-radius:50%;background:var(--orange)}
.nav a{position:absolute;top:29px;font-size:13.5px;color:var(--ink);text-decoration:none}
.nav a.active{color:var(--orange);border-bottom:2px solid var(--orange);padding-bottom:3px}
.contact-pill{left:940px;top:17px;width:118px;height:36px;border-radius:18px;background:var(--white);color:var(--orange);font-size:11.5px;box-shadow:0 2px 8px rgba(0,0,0,.12);z-index:4}

/* hero */
.hero{left:0;top:0;width:1200px;height:557px;background:var(--ivory)}
.hero h1{left:141px;top:208px;font-size:32px;font-weight:600;line-height:47px;color:var(--ink)}
.hero h1 span{color:var(--orange)}
.hero-sub{left:141px;top:365px;border-left:2px solid var(--orange);padding-left:11px;font-size:13px;line-height:23px;width:430px}
.hero .btn{left:141px;top:432px;width:162px;height:33px;border-radius:17px;font-size:12px;letter-spacing:.5px}

/* services */
.frame{position:absolute;background:var(--ivory);box-shadow:0 0 10px rgba(0,0,0,.04)}
.frame-inner{position:absolute;left:14px;top:14px;right:14px;bottom:14px;background:var(--white)}
.photo{position:absolute}
.icon-badge{position:absolute;width:64px;height:64px;border-radius:50%;background:var(--orange)}
.svc-title{position:absolute;font-size:31px;font-weight:600;color:#333}
.svc-text{position:absolute;font-size:12.5px;line-height:22px;color:var(--text);width:380px}
.svc-btn{width:114px;height:38px}

/* about */
.about{left:0;top:2195px;width:1200px;height:626px}
.about-card{left:609px;top:2278px;width:449px;height:454px;border-radius:10px;background:rgba(10,10,10,.88);border:1px solid rgba(255,255,255,.5);color:var(--white);padding:0 40px}
.about-card h3{position:absolute;left:40px;top:52px;font-size:22px;font-weight:600}
.about-card h2{position:absolute;left:38px;top:94px;font-size:34px;font-weight:600}
.about-card .rule{position:absolute;left:40px;top:146px;width:60px;height:2px;background:var(--orange)}
.about-card p{position:absolute;left:40px;width:380px;font-size:12px;line-height:20.5px}
.about-card .btn{left:38px;top:357px;width:103px;height:38px}

/* reviews */
.reviews-title{left:0;top:2905px;width:1200px;text-align:center;font-size:34px;font-weight:600}
.reviews-rule{left:575px;top:2967px;width:50px;height:2px;background:var(--orange)}
.review{position:absolute;top:3023px;width:432px;height:252px;background:var(--white);box-shadow:0 4px 14px rgba(0,0,0,.1);text-align:center}
.review::after{content:"";position:absolute;left:22px;right:22px;bottom:-7px;height:7px;background:#555;border-radius:0 0 4px 4px}
.avatar{position:absolute;left:177px;top:-30px;width:78px;height:78px;border-radius:50%;border:3px solid var(--orange);background:linear-gradient(#c9b8a6,#8c735f)}
.review h4{position:absolute;left:0;right:0;top:66px;font-size:19px;font-weight:600}
.review p{position:absolute;left:34px;right:34px;top:102px;font-size:12px;line-height:21px;color:var(--text)}
.quote{position:absolute;right:12px;bottom:12px}
.arrow{position:absolute;top:3128px;width:22px;height:22px;border-radius:50%;background:var(--white);box-shadow:0 1px 4px rgba(0,0,0,.25)}

/* cta */
.footer{left:0;top:3558px;width:1200px;height:413px;background:var(--black);color:var(--white)}
.cta{left:190px;top:3364px;width:820px;height:246px;background:var(--orange);z-index:2}
.cta-border{position:absolute;left:54px;top:41px;width:712px;height:150px;border:1px solid var(--white)}
.cta h2{position:absolute;left:0;right:0;top:84px;text-align:center;font-size:30px;font-weight:600;line-height:42px;color:#1a1a1a}
.cta .btn{left:359px;top:172px;width:102px;height:36px;background:var(--white);color:var(--ink);font-size:11.5px}

.f-head{position:absolute;top:126px;font-size:16px;font-weight:600}
.f-links{position:absolute;left:143px;top:160px;list-style:none}
.f-links li{font-size:12px;height:33px;padding-left:18px;position:relative}
.f-links li::before{content:"›";position:absolute;left:0;top:-2px;font-size:14px}
.f-contact{position:absolute;left:473px;display:flex;gap:12px}
.f-icon{width:28px;height:28px;border-radius:50%;background:var(--orange);display:flex;align-items:center;justify-content:center;flex:none}
.f-contact b{display:block;font-size:13px;font-weight:600;margin-bottom:4px}
.f-contact span{font-size:12px;line-height:19px}
.f-brand{position:absolute;left:877px;top:172px;width:180px;display:flex;align-items:center;gap:8px;color:var(--orange);font-size:22px;font-weight:700;line-height:26px}
.socials{position:absolute;left:898px;top:276px;display:flex;gap:8px}
.socials i{width:28px;height:28px;border-radius:50%;border:1.5px solid var(--orange);display:block}
.f-rule{position:absolute;left:143px;top:356px;width:914px;height:1px;background:#333}
.copy{position:absolute;left:0;top:380px;width:1200px;text-align:center;font-size:12px;color:#ccc}
</style>
</head>
<body>

<section class="hero abs">
  <svg class="abs" style="left:640px;top:0" width="560" height="557" viewBox="0 0 560 557" role="img" aria-label="Photo of lawn sprinklers watering green grass at sunset">
    <defs>
      <linearGradient id="lawn" x1="0" y1="0" x2="0" y2="1">
        <stop offset="0" stop-color="#c9d6a8"/>
        <stop offset=".45" stop-color="#9bb75a"/>
        <stop offset="1" stop-color="#3f6a1f"/>
      </linearGradient>
    </defs>
    <path d="M212 0 C190 70 150 110 80 160 C10 210 -10 300 30 360 C70 420 160 380 210 420 C270 470 300 540 420 545 C480 548 530 535 560 525 L560 0 Z" fill="url(#lawn)" stroke="var(--orange)" stroke-width="6"/>
  </svg>
  <h1 class="abs">Welcome To <span>Fenwick Grading</span><br>Your One-Stop Solution For<br>Home Improvement</h1>
  <p class="hero-sub abs">Expertise In Irrigation Systems, Landscape Lighting, And Buried Service Wire Installation</p>
  <a class="btn">GET A FREE QUOTE</a>
</section>

<header class="header abs">
  <div class="brand abs" style="left:140px;top:26px"><i class="brand-dot"></i>Fenwick Grading LTD</div>
  <nav class="nav">
    <a class="active" style="left:385px">Home</a>
    <a style="left:452px">Irrigation</a>
    <a style="left:539px">Landscape Lighting</a>
    <a style="left:694px">Buried Service Wire</a>
  </nav>
</header>
<a class="btn contact-pill">CONTACT US</a>

<svg class="abs" style="left:468px;top:598px" width="264" height="24" viewBox="0 0 264 24">
  <path d="M0 2 L264 2 C200 8 160 20 132 20 C104 20 64 8 0 2 Z" fill="var(--orange)"/>
  <path d="M100 14 C120 20 144 20 164 14 L132 22 Z" fill="#4a6a22"/>
</svg>

<!-- Service 1 -->
<div class="frame" style="left:247px;top:690px;width:815px;height:436px"><div class="frame-inner"></div></div>
<div class="photo" style="left:143px;top:741px;width:423px;height:333px;background:linear-gradient(160deg,#a9a08f,#7aa33f 55%,#4f7a26)" role="img" aria-label="Photo of a sprinkler spraying a lawn beside a gravel bed"></div>
<div class="icon-badge" style="left:618px;top:761px"></div>
<h2 class="svc-title" style="left:618px;top:840px">Irrigation Systems</h2>
<p class="svc-text" style="left:618px;top:883px">Our irrigation systems are designed to provide your lawn and garden with the right amount of water, without wasting a single drop. With our expert installation and service, you can rest assured that your plants will receive the nourishment they need to thrive.</p>
<a class="btn svc-btn" style="left:618px;top:1006px">Learn More</a>

<!-- Service 2 -->
<div class="frame" style="left:137px;top:1180px;width:813px;height:435px"><div class="frame-inner"></div></div>
<div class="icon-badge" style="left:196px;top:1250px"></div>
<h2 class="svc-title" style="left:196px;top:1329px">Landscape Lighting</h2>
<p class="svc-text" style="left:196px;top:1372px">Our landscape lighting solutions are designed to enhance the beauty and functionality of your outdoor space. From subtle pathway lighting to dramatic spotlights, we'll work with you to create a lighting plan that meets your needs and complements your landscape</p>
<a class="btn svc-btn" style="left:196px;top:1501px">Learn More</a>
<div class="photo" style="left:633px;top:1230px;width:424px;height:333px;background:radial-gradient(circle at 45% 35%,#c9a659,#3b4a22 55%,#1c2412)" role="img" aria-label="Photo of a garden path lit by landscape lights at night"></div>

<!-- Service 3 -->
<div class="frame" style="left:247px;top:1668px;width:815px;height:436px"><div class="frame-inner"></div></div>
<div class="photo" style="left:141px;top:1718px;width:423px;height:333px;background:linear-gradient(135deg,#3a3f43,#6d6258 55%,#b59a70)" role="img" aria-label="Photo of a technician installing equipment in a home kitchen"></div>
<div class="icon-badge" style="left:617px;top:1738px"></div>
<h2 class="svc-title" style="left:617px;top:1817px">Buried Service Wire</h2>
<p class="svc-text" style="left:617px;top:1860px">Our team of experienced professionals will install your buried service wire and drainage with precision and care. We'll work with you to ensure that your home is equipped with the latest technology, providing you with safe and reliable power, water flow, and utility services</p>
<a class="btn svc-btn" style="left:617px;top:1985px">Learn More</a>

<!-- About -->
<section class="about abs" role="img" aria-label="Photo of a house with a green lawn and flowering shrubs" style="background:linear-gradient(180deg,#7d8f86 0%,#4d6b3a 45%,#3f7a25 80%,#5b9a2e 100%)"></section>
<div class="about-card abs">
  <h3>About</h3>
  <h2>Fenwick Grading Ltd</h2>
  <div class="rule"></div>
  <p style="top:178px">Lorem ipsum dolor sit amet, consectetur adipiscing elit sed do eiusmod tempor incididunt ut labore et dolore magna aliqua Ut enim ad minim veniam quis</p>
  <p style="top:246px">Lorem ipsum dolor sit amet, consectetur adipiscing elit sed do eiusmod tempor incididunt ut labore et dolore magna aliqua Ut enim ad minim veniam quis "Lorem ipsum dolor sit amet, consectetur adipiscing elit sed do eiusmod tempor incididunt ut labore et dolore magna aliqua</p>
  <a class="btn">Contact Us</a>
</div>

<!-- Reviews -->
<h2 class="reviews-title abs">Customer Reviews</h2>
<div class="reviews-rule abs"></div>
<div class="arrow" style="left:133px"></div>
<div class="arrow" style="left:1046px"></div>
<article class="review" style="left:143px">
  <div class="avatar" role="img" aria-label="Customer portrait"></div>
  <h4>Marcus Hale</h4>
  <p>Lorem Ipsum is simply dummy text of the printing and typesetting industry. Lorem Ipsum has been the industry's standard dummy text ever since the 1500s, when an unknown printer took a galley of type and scrambledstandard dummy text ever since standard dummy text ever since</p>
  <svg class="quote" width="42" height="34" viewBox="0 0 42 34"><path d="M2 2h16v16c0 8-5 14-14 15l-1-5c5-1 7-4 7-8H2z M24 2h16v16c0 8-5 14-14 15l-1-5c5-1 7-4 7-8h-8z" fill="var(--peach)"/></svg>
</article>
<article class="review" style="left:625px">
  <div class="avatar" role="img" aria-label="Customer portrait"></div>
  <h4>Nora Briggs</h4>
  <p>Lorem Ipsum is simply dummy text of the printing and typesetting industry. Lorem Ipsum has been the industry's standard dummy text ever since the 1500s, when an unknown printer took a galley of type and scrambled standard dummy text ever since standard dummy text ever since</p>
  <svg class="quote" width="42" height="34" viewBox="0 0 42 34"><path d="M2 2h16v16c0 8-5 14-14 15l-1-5c5-1 7-4 7-8H2z M24 2h16v16c0 8-5 14-14 15l-1-5c5-1 7-4 7-8h-8z" fill="var(--peach)"/></svg>
</article>

<!-- Footer -->
<footer class="footer abs">
  <h4 class="f-head" style="left:143px">Quick Links</h4>
  <ul class="f-links">
    <li>Home</li><li>Irrigation</li><li>Landscape Lighting</li><li>Buried Service Wire</li><li>Contact Us</li>
  </ul>
  <h4 class="f-head" style="left:473px">Contact Details</h4>
  <div class="f-contact" style="top:160px">
    <i class="f-icon"><svg width="12" height="14" viewBox="0 0 12 14"><path d="M6 0a5 5 0 0 0-5 5c0 4 5 9 5 9s5-5 5-9a5 5 0 0 0-5-5zm0 7a2 2 0 1 1 0-4 2 2 0 0 1 0 4z" fill="#fff"/></svg></i>
    <span>12 Lorem Imsum, Street Name,<br>City Name, Country – 12345</span>
  </div>
  <div class="f-contact" style="top:216px">
    <i class="f-icon"><svg width="12" height="12" viewBox="0 0 12 12"><path d="M2.5 0.5l2 2.2-1 1.4c.7 1.6 1.8 2.7 3.4 3.4l1.4-1 2.2 2-1 2.3C5 10.5 1.5 7 .4 1.5z" fill="#fff"/></svg></i>
    <div><b>Phone</b><span>123.456.7890</span></div>
  </div>
  <div class="f-contact" style="top:270px">
    <i class="f-icon"><svg width="13" height="10" viewBox="0 0 13 10"><rect x=".5" y=".5" width="12" height="9" rx="1" fill="#fff"/><path d="M1 1l5.5 4.5L12 1" stroke="var(--orange)" fill="none"/></svg></i>
    <div><b>Email</b><span>fenwickgrading@mailbox-example.net</span></div>
  </div>
  <div class="f-brand"><i class="brand-dot" style="flex:none"></i>Fenwick Grading LTD</div>
  <div class="socials"><i></i><i></i><i></i><i></i></div>
  <div class="f-rule"></div>
  <p class="copy">© 2024 Fenwick Grading Ltd . All Rights Reserved.</p>
</footer>

<section class="cta abs">
  <div class="cta-border"></div>
  <h2>Expertise In Irrigation Systems, Landscape<br>Lighting, And Buried Service Wire</h2>
  <a class="btn">Contact Us</a>
</section>

</body>
</html>
```